Tree Pruning Website

We need a website for a tree Arborist, pruning company called Maple Crest Canopy Works. We look after all types of trees, knock down trees and prune trees. Our target market is from domestic clients to government clients and everything in between.

We would like to see the use of our main colours which are orange and green

We are not looking forward in seeing a template that we have seen before but a unique template. We have designed 5 templates ourselves and we wish for the design community to take our designs to the next level.

We have also designed a template for things that **we are not** looking for (Version 4)

To make it fair for everyone, we are also not giving out any participation payments as we have had. One winner will take all of the payment!!!

I Have attached a image of the designs and a image of a tree.

We are just looking at the PSD file been developed. We have our own team who can slice the image up into a HTML format.

Target Market(s)

Everyone who needs to cut down a tree

Industry/Entity Type

Government

Requirements
Must have
• Logo on front page
A List of our services
jQuery slider on page
Phone Number on every page

```html
<!DOCTYPE html>
<html lang="en">
<head>
<meta charset="utf-8">
<title>Maple Crest Canopy Works</title>
<link href="https://fonts.googleapis.com/css2?family=Arvo:wght@400;700&family=Open+Sans:wght@400;600;700&family=Arimo:wght@400;700&family=Roboto+Condensed:wght@400&display=swap" rel="stylesheet">
<style>
:root{
  --olive:#6f7b0c;
  --olive-dark:#4a5206;
  --lime:#a6b91a;
  --orange:#f0a30a;
  --orange-dark:#d98700;
  --orange-deep:#c77a00;
  --ink:#3b3b3b;
  --body:#5e5e5e;
  --grey-band:#eceef1;
  --card:#eef0f3;
  --footer:#3d3d3d;
  --footer-base:#2c2c2c;
  --footer-text:#8b8b8b;
  --white:#ffffff;
}
*{margin:0;padding:0;box-sizing:border-box}
html,body{width:924px;height:1200px;overflow:hidden;background:var(--white)}
body{position:relative;font-family:"Open Sans",sans-serif;color:var(--body)}
.abs{position:absolute}

/* header */
.top-band{left:0;top:0;width:924px;height:328px;background:var(--olive)}
.brand{left:236px;top:40px;display:flex;align-items:center;gap:8px}
.brand-dot{width:22px;height:22px;border-radius:50%;background:var(--orange)}
.brand-name{font-family:"Arimo",sans-serif;font-weight:700;font-size:15px;color:var(--orange);line-height:1.1;width:120px}
.main-nav{left:424px;top:70px;display:flex;gap:15px;font-family:"Arimo",sans-serif;font-size:7.5px;color:var(--white)}
.main-nav a{color:var(--white);text-decoration:none;position:relative}
.main-nav a.active::after{content:"";position:absolute;left:-2px;right:-2px;top:13px;height:3px;background:var(--orange)}

/* slider */
.slider{left:236px;top:99px;width:452px;height:229px;border:2px solid var(--lime);border-bottom:none;
  background:linear-gradient(160deg,#7f9a56 0%,#a7b57a 25%,#8c6a3a 55%,#5a3e1e 80%,#7a8a45 100%)}
.slider-arrow{width:26px;height:26px;border-radius:50%;border:2px solid var(--orange);display:flex;align-items:center;justify-content:center}
.slider-dots{left:440px;top:312px;display:flex;gap:5px}
.slider-dots span{width:10px;height:10px;border-radius:50%;background:#3a3a3a;border:2px solid #d8d8d8}
.slider-dots span.on{background:var(--olive);border-color:#d8e08a}

/* call bar */
.call-bar{left:236px;top:328px;width:452px;height:58px;background:var(--orange);box-shadow:0 10px 14px -8px rgba(0,0,0,.35)}
.call-text{left:8px;top:9px;width:295px;font-family:"Arimo",sans-serif;font-size:10.5px;line-height:14px;color:var(--white)}
.call-text b{color:#2f2a10}
.call-phone{left:303px;top:0;width:149px;height:58px;background:linear-gradient(90deg,var(--orange-deep),var(--orange));display:flex;align-items:center;gap:9px;padding-left:10px}
.phone-badge{width:32px;height:32px;border-radius:50%;background:var(--olive-dark);border:3px solid #c6d36a;display:flex;align-items:center;justify-content:center}
.phone-number{font-family:"Roboto Condensed",sans-serif;font-size:18px;color:var(--white)}

/* sectors */
.sector{width:112px;text-align:center}
.sector-icon{width:32px;height:32px;margin:0 auto;border-radius:50%;background:var(--olive-dark);border:3px solid var(--orange);display:flex;align-items:center;justify-content:center}
.sector h3{font-family:"Arvo",serif;font-weight:400;font-size:11px;color:var(--ink);margin-top:11px;letter-spacing:.3px}
.sector p{font-size:5.8px;line-height:10px;margin-top:8px;color:var(--body)}
.btn{display:inline-block;background:var(--orange);color:var(--white);font-size:6.5px;font-weight:600;padding:4px 6px;border-radius:2px;border-bottom:2px solid var(--orange-dark)}
.sector .btn{margin-top:9px}

/* overview */
.overview{left:236px;top:602px;width:442px}
.section-title{font-family:"Arvo",serif;font-weight:400;font-size:10.5px;color:var(--ink)}
.overview p{font-size:5.8px;line-height:8.8px;margin-top:8px}
.overview p:first-of-type{margin-top:11px}
.hl{color:var(--lime)}
.read-more{left:634px;top:723px}

/* services & testimonials */
.rule-top{height:1px;background:#dedede}
.green-rule{height:4px;background:var(--lime)}
.green-notch{width:0;height:0;border-left:7px solid var(--lime);border-bottom:7px solid transparent}
.nav-pair{display:flex;gap:2px}
.nav-pair span{width:12px;height:12px;border-radius:50%;border:1px solid #d0d0d0;display:flex;align-items:center;justify-content:center}
.service-card{width:106px;height:113px;background:var(--card)}
.service-photo{width:106px;height:81px;border:3px solid var(--orange)}
.service-card .cap-notch{position:absolute;left:0;top:81px;border-left:6px solid var(--lime);border-bottom:6px solid transparent}
.service-card h4{font-family:"Arvo",serif;font-weight:400;font-size:7.5px;color:var(--ink);margin:9px 0 0 4px}
.service-card small{display:block;font-family:"Arvo",serif;font-size:5.5px;color:#888;margin-left:4px}
.quote-box{left:582px;top:819px;width:106px;height:79px;background:#f6f7f9;border:1px solid #d6d6d6;padding:10px 7px;font-size:5.8px;line-height:8.7px;font-style:italic;color:#8c8c8c}
.quote-tail{left:594px;top:897px}
.quote-author{left:598px;top:920px;display:flex;align-items:center;gap:5px;font-size:6.2px;color:var(--ink)}

/* tweet band */
.tweet-band{left:0;top:954px;width:924px;height:49px;background:var(--grey-band)}
.tweet-mark{left:254px;top:964px;width:24px;height:24px;border-radius:50%;background:#3a3a3a}
.tweet-text{left:301px;top:964px;font-size:7.5px;line-height:10px;color:var(--ink);width:400px}

/* footer */
.footer{left:0;top:1003px;width:924px;height:175px;background:var(--footer)}
.footer-notch{left:242px;top:1003px}
.footer-col{top:1028px}
.footer-col h5{font-family:"Arvo",serif;font-weight:400;font-size:7.5px;color:var(--white);margin-bottom:10px}
.footer-col p{font-size:5.3px;line-height:8.6px;color:var(--footer-text)}
.news-item{padding-bottom:6px;margin-bottom:6px;border-bottom:1px solid #4b4b4b;width:97px}
.news-item.hl p{color:#c7d33a}
.thumb{width:27px;height:27px;border:2px solid #eeeeee}
.map{left:585px;top:1053px;width:103px;height:54px;border:2px solid #bdbdbd;background:linear-gradient(135deg,#e8e4d8,#d7e3c8 60%,#e6dfcf)}
.contact-line{font-size:5.3px;color:#bdbdbd;display:flex;align-items:center;gap:6px}
.footer-base{left:0;top:1178px;width:924px;height:22px;background:var(--footer-base)}
.copyright{left:236px;top:1184px;font-size:5.3px;color:var(--footer-text)}
.social{top:1184px;width:8px;height:8px;background:#777}
</style>
</head>
<body>

<div class="abs top-band"></div>
<div class="abs brand">
  <div class="brand-dot"></div>
  <div class="brand-name">Maple Crest Canopy Works</div>
</div>
<nav class="abs main-nav">
  <a class="active">Home</a><a>About Us</a><a>Our Services</a><a>Get A quote</a><a>Our Work</a><a>Contact Us</a>
</nav>

<div class="abs slider" role="img" aria-label="Photo looking up a large tree trunk into its spreading canopy"></div>
<div class="abs slider-arrow" style="left:201px;top:180px">
  <svg width="12" height="10" viewBox="0 0 12 10"><path d="M11 5H2M5 1L1 5l4 4" stroke="#f2e6c0" stroke-width="2" fill="none"/></svg>
</div>
<div class="abs slider-arrow" style="left:698px;top:180px">
  <svg width="12" height="10" viewBox="0 0 12 10"><path d="M1 5h9M7 1l4 4-4 4" stroke="#f2e6c0" stroke-width="2" fill="none"/></svg>
</div>
<div class="abs slider-dots"><span class="on"></span><span></span><span></span></div>

<div class="abs call-bar">
  <p class="abs call-text">Maple Crest is the leading tree pruning services located Perth. Our motto is when you call, we <b>guarantee</b> to turn up and <b>provide care</b> to our customers.</p>
  <div class="abs call-phone">
    <div class="phone-badge">
      <svg width="14" height="14" viewBox="0 0 24 24"><path d="M6.6 10.8a15 15 0 0 0 6.6 6.6l2.2-2.2c.3-.3.7-.4 1-.2 1.1.4 2.3.6 3.6.6.6 0 1 .4 1 1V20c0 .6-.4 1-1 1A17 17 0 0 1 3 4c0-.6.4-1 1-1h3.5c.6 0 1 .4 1 1 0 1.2.2 2.4.6 3.6.1.3 0 .7-.2 1z" fill="#fff"/></svg>
    </div>
    <span class="phone-number">08 5550 0142</span>
  </div>
</div>

<section>
  <div class="abs sector" style="left:233px;top:434px">
    <div class="sector-icon"><svg width="12" height="14" viewBox="0 0 12 14"><rect x="2" y="3" width="8" height="10" rx="1" fill="#f3e7c2"/><rect x="4" y="0.5" width="4" height="3" fill="none" stroke="#f3e7c2"/></svg></div>
    <h3>DOMESTIC</h3>
    <p>At vero eos et accusam et justo duo dolores et ea rebum. Stet clita kasd gubergren, no sea takimata sanctus est Lorem ipsum dolor sit amet.</p>
    <span class="btn">Learn more</span>
  </div>
  <div class="abs sector" style="left:348px;top:434px">
    <div class="sector-icon"><svg width="16" height="11" viewBox="0 0 16 11"><path d="M1 1h6v9H1zM9 1h6v9H9z" fill="#f3e7c2"/></svg></div>
    <h3>COMMERCIAL</h3>
    <p>Ut wisi enim ad minim veniam, quis nostrud exerci tation ullamcorper suscipit lobortis nisl ut aliquip ex ea commodo consequat.</p>
    <span class="btn">Learn more</span>
  </div>
  <div class="abs sector" style="left:464px;top:434px">
    <div class="sector-icon"><svg width="14" height="14" viewBox="0 0 14 14"><circle cx="7" cy="4" r="3" fill="#f3e7c2"/><path d="M1 13c0-4 2.5-5.5 6-5.5s6 1.5 6 5.5z" fill="#f3e7c2"/></svg></div>
    <h3>GOVERMENT</h3>
    <p>Nam liber tempor cum soluta nobis eleifend option congue nihil imperdiet doming id quod mazim placerat facer possim assum.</p>
    <span class="btn">Learn more</span>
  </div>
  <div class="abs sector" style="left:579px;top:434px">
    <div class="sector-icon"><svg width="14" height="14" viewBox="0 0 14 14"><path d="M2 12C2 5 6 2 12 2c0 6-3 10-10 10z" fill="none" stroke="#f3e7c2" stroke-width="1.5"/><path d="M2 12l6-6" stroke="#f3e7c2"/></svg></div>
    <h3>NON PROFIT</h3>
    <p>Lorem ipsum dolor sit amet, consetetur sadipscing elitr, sed diam nonumy eirmod tempor invidunt ut labore et dolore.</p>
    <span class="btn">Learn more</span>
  </div>
</section>

<section class="abs overview">
  <h2 class="section-title">Company Overview</h2>
  <p><span class="hl">Duis autem vel eum iriure</span> dolor in hendrerit in vulputate velit esse molestie consequat, vel illum dolore eu feugiat nulla facilisis at vero eros et accumsan et iusto odio dignissim qui blandit praesent luptatum zzril delenit augue duis dolore te feugait nulla facilisi. Lorem ipsum dolor sit amet, consectetuer adipiscing elit, sed diam nonummy nibh euismod tincidunt ut laoreet dolore magna aliquam erat volutpat.</p>
  <p>Ut wisi enim ad minim veniam, quis nostrud exerci tation ullamcorper suscipit lobortis nisl ut <span class="hl">aliquip ex ea commodo consequat</span>. Duis autem vel eum iriure dolor in hendrerit in vulputate velit esse molestie consequat, vel illum dolore eu feugiat nulla facilisis at vero eros et accumsan et iusto odio dignissim qui blandit praesent luptatum zzril delenit augue duis dolore te feugait nulla facilisi. Nam liber tempor cum soluta nobis eleifend option congue nihil imperdiet doming id quod mazim placerat facer possim assum. Lorem ipsum dolor sit amet, consectetuer adipiscing elit, sed diam nonummy nibh euismod tincidunt.</p>
  <p class="hl">Ut laoreet dolore magna aliquam erat volutpat. Ut wisi enim ad minim veniam, quis nostrud exerci tation ullamcorper suscipit lobortis nisl ut aliquip ex ea commodo consequat.</p>
</section>
<span class="abs btn read-more">Read more</span>

<!-- services -->
<div class="abs rule-top" style="left:236px;top:771px;width:337px"></div>
<h2 class="abs section-title" style="left:236px;top:776px">Our Services</h2>
<div class="abs nav-pair" style="left:545px;top:777px">
  <span><svg width="6" height="5" viewBox="0 0 6 5"><path d="M6 2.5H1M3 .5l-2 2 2 2" stroke="#ccc" fill="none"/></svg></span>
  <span><svg width="6" height="5" viewBox="0 0 6 5"><path d="M0 2.5h5M3 .5l2 2-2 2" stroke="#ccc" fill="none"/></svg></span>
</div>
<div class="abs green-rule" style="left:236px;top:795px;width:337px"></div>
<div class="abs green-notch" style="left:236px;top:799px"></div>

<div class="abs service-card" style="left:236px;top:819px">
  <div class="service-photo" role="img" aria-label="Pale gum tree trunks reaching into the sky" style="background:linear-gradient(160deg,#c9d3de,#8e9a7c 60%,#6a7048)"></div>
  <span class="cap-notch"></span><h4>Observation 1</h4><small>Locations</small>
</div>
<div class="abs service-card" style="left:351px;top:819px">
  <div class="service-photo" role="img" aria-label="Dense green leaves with red berries under a tree canopy" style="background:linear-gradient(160deg,#3d4a1e,#6e8a2e 50%,#2a2e18)"></div>
  <span class="cap-notch"></span><h4>Observation 1</h4><small>Locations</small>
</div>
<div class="abs service-card" style="left:467px;top:819px">
  <div class="service-photo" role="img" aria-label="Sunlit forest path lined with green trees" style="background:linear-gradient(180deg,#4e6a1c,#a7b65a 55%,#6d5b34)"></div>
  <span class="cap-notch"></span><h4>Observation 1</h4><small>Locations</small>
</div>

<!-- testimonials -->
<div class="abs rule-top" style="left:585px;top:771px;width:103px"></div>
<h2 class="abs section-title" style="left:585px;top:776px">Testimonials</h2>
<div class="abs nav-pair" style="left:661px;top:777px">
  <span><svg width="6" height="5" viewBox="0 0 6 5"><path d="M6 2.5H1M3 .5l-2 2 2 2" stroke="#ccc" fill="none"/></svg></span>
  <span><svg width="6" height="5" viewBox="0 0 6 5"><path d="M0 2.5h5M3 .5l2 2-2 2" stroke="#ccc" fill="none"/></svg></span>
</div>
<div class="abs green-rule" style="left:582px;top:795px;width:106px"></div>
<div class="abs green-notch" style="left:582px;top:799px"></div>
<blockquote class="abs quote-box">" Duis autem vel eum iriure dolor in hendrerit in feugiat nulla facilisis at vero eros et accumsan vulputate velit esse molestie consequat, vel illum dolore eu pasto. "</blockquote>
<svg class="abs quote-tail" width="16" height="14" viewBox="0 0 16 14"><path d="M0 0h16L2 13z" fill="#f6f7f9"/><path d="M0 0l2 13L16 0" fill="none" stroke="#d6d6d6"/></svg>
<div class="abs quote-author">
  <svg width="12" height="12" viewBox="0 0 14 14"><circle cx="7" cy="4" r="3" fill="#333"/><path d="M1 13c0-4 2.5-5.5 6-5.5s6 1.5 6 5.5z" fill="#333"/></svg>
  <span><b>Alan Brice</b> - Goverment -</span>
</div>

<!-- tweet band -->
<div class="abs tweet-band"></div>
<div class="abs tweet-mark"></div>
<p class="abs tweet-text"><span class="hl">@maplecrestcanopy</span> Stet clita kasd gubergren, no sea takimata sanctus est Lorem ipsum....by <span class="hl">maplecrestcanopy</span><br>about 2 hour ago</p>

<!-- footer -->
<footer>
  <div class="abs footer"></div>
  <svg class="abs footer-notch" width="32" height="16" viewBox="0 0 32 16"><path d="M0 0h32L0 16z" fill="#eceef1"/></svg>

  <div class="abs footer-col" style="left:236px;width:100px">
    <h5>ABOUT US</h5>
    <p>Lorem ipsum dolor sit amet, consetetur sadipscing elitr, sed diam nonumy eirmod tempor invidunt ut labore et dolore magna aliquyam erat, sed diam voluptua. At vero eos et accusam et justo duo dolores et ea rebum. Stet clita kasd gubergren, no sea takimata sanctus est Lorem ipsum dolor sit amet</p>
  </div>

  <div class="abs footer-col" style="left:351px">
    <h5>LATEST NEWS</h5>
    <div class="news-item"><p>Lorem ipsum dolor sit amet, consetetur sadipscing elitr, sed diam.</p></div>
    <div class="news-item hl"><p>Nonumy eirmod tempor invidunt ut.</p></div>
    <div class="news-item"><p>Labore et dolore magna aliquyam erat, sed diam voluptua.</p></div>
    <div class="news-item"><p>At vero eos et accusam et justo duo dolores et ea rebum.</p></div>
  </div>

  <div class="abs footer-col" style="left:467px">
    <h5>GALLERY</h5>
  </div>
  <div class="abs thumb" style="left:467px;top:1053px;background:linear-gradient(#dfeefa,#3d8fc4)" role="img" aria-label="Water drop on a sprout"></div>
  <div class="abs thumb" style="left:507px;top:1053px;background:linear-gradient(#e9c9a8,#b5714a)" role="img" aria-label="Portrait photo"></div>
  <div class="abs thumb" style="left:545px;top:1053px;background:linear-gradient(#2f6a5a,#8fbf5a)" role="img" aria-label="Green landscape"></div>
  <div class="abs thumb" style="left:467px;top:1091px;background:linear-gradient(#f0f4d8,#8cbf3a)" role="img" aria-label="Fresh grass"></div>
  <div class="abs thumb" style="left:507px;top:1091px;background:linear-gradient(#7fa23a,#3d5a1a)" role="img" aria-label="Leaves close up"></div>
  <div class="abs thumb" style="left:545px;top:1091px;background:linear-gradient(#c9b89a,#6a8a4a)" role="img" aria-label="Outdoor portrait"></div>
  <span class="abs btn" style="left:527px;top:1132px">more gallery</span>

  <div class="abs footer-col" style="left:585px">
    <h5>GET IN TOUCH</h5>
  </div>
  <div class="abs map" role="img" aria-label="Street map showing the office location"></div>
  <div class="abs" style="left:587px;top:1117px">
    <p class="contact-line" style="color:var(--footer-text);display:block;line-height:8px">14 Ridgeway Lane<br>BRAMBLEFORD, WA 6000</p>
    <p class="contact-line" style="margin-top:6px">
      <svg width="7" height="7" viewBox="0 0 24 24"><path d="M6.6 10.8a15 15 0 0 0 6.6 6.6l2.2-2.2c.3-.3.7-.4 1-.2 1.1.4 2.3.6 3.6.6.6 0 1 .4 1 1V20c0 .6-.4 1-1 1A17 17 0 0 1 3 4c0-.6.4-1 1-1h3.5c.6 0 1 .4 1 1 0 1.2.2 2.4.6 3.6.1.3 0 .7-.2 1z" fill="#999"/></svg>08 5550 0178</p>
    <p class="contact-line" style="margin-top:4px">
      <svg width="7" height="7" viewBox="0 0 8 8"><rect x="1" y="1" width="6" height="6" fill="none" stroke="#999"/><path d="M2 3h4M2 5h4" stroke="#999"/></svg>08 5550 0178</p>
    <p class="contact-line" style="margin-top:4px;color:var(--footer-text)">
      <svg width="7" height="6" viewBox="0 0 8 6"><rect x=".5" y=".5" width="7" height="5" fill="none" stroke="#999"/><path d="M.5.5L4 3.5 7.5.5" stroke="#999" fill="none"/></svg>hello@maplecrest.example</p>
  </div>

  <div class="abs footer-base"></div>
  <p class="abs copyright">© Copyright 2013 maplecrestcanopy.</p>
  <span class="abs social" style="left:647px"></span>
  <span class="abs social" style="left:663px"></span>
  <span class="abs social" style="left:679px"></span>
</footer>

</body>
</html>
```